Design a New Business Card for Our Company

We are looking for fresh, unique, and a modern business card that reflects our roots as digital marketing agency focused on SEM.

Industry/Entity Type

Marketing

Contact Information for Business Card

looking for very unique out of the box designs. clean and modern that compliments our logo

Requirements
Must have
• colors should match our logo
• Front should have name, address, email, and phone/fax of the person, phone/fax are the same number
• back should have our url

```html
<!DOCTYPE html>
<html lang="en">
<head>
<meta charset="utf-8">
<title>Lumenreach Media – Business Card</title>
<link href="https://fonts.googleapis.com/css2?family=Montserrat:wght@400;500;600;700&display=swap" rel="stylesheet">
<style>
  :root {
    --backdrop: #2a2a2b;
    --card: #050505;
    --blue: #5b9bd5;
    --grey: #c4c4c4;
    --white: #f2f2f2;
  }
  * { margin: 0; padding: 0; box-sizing: border-box; }
  html, body {
    width: 1200px; height: 900px; overflow: hidden;
    background: var(--backdrop);
    font-family: "Montserrat", sans-serif;
  }
  .canvas { position: relative; width: 1200px; height: 900px; }
  .card {
    position: absolute; left: 270px;
    width: 660px; height: 377px;
    background: var(--card);
    border-radius: 22px;
    box-shadow: 0 14px 30px rgba(0,0,0,0.55);
    overflow: hidden;
  }
  .card--back { top: 60px; }
  .card--front { top: 463px; }

  /* Back side */
  .back-brand {
    position: absolute; left: 0; right: 0; top: 100px;
    display: flex; flex-direction: column; align-items: center; gap: 18px;
  }
  .back-brand__dot {
    width: 70px; height: 70px; border-radius: 50%; background: var(--blue);
  }
  .back-brand__name {
    font-weight: 700; font-size: 32px; color: var(--grey); letter-spacing: 0.5px;
  }
  .back-url {
    position: absolute; left: 0; right: 0; bottom: 34px;
    text-align: center; font-size: 17px; font-weight: 500; color: var(--white);
  }
  .back-url span { color: var(--blue); }

  /* Front side */
  .front-brand {
    position: absolute; left: 36px; top: 212px;
    display: flex; align-items: center; gap: 12px;
    white-space: nowrap;
  }
  .front-brand__dot {
    width: 34px; height: 34px; border-radius: 50%; background: var(--blue);
  }
  .front-brand__name {
    font-weight: 700; font-size: 24px; color: var(--blue); line-height: 1;
  }
  .divider {
    position: absolute; left: 360px; top: 56px; width: 2px; height: 250px;
    background: var(--blue);
  }
  .contact {
    position: absolute; left: 382px; top: 58px; right: 20px;
    color: var(--white); white-space: nowrap;
  }
  .contact__name {
    font-weight: 600; font-size: 24px; color: var(--blue); letter-spacing: 0.5px;
  }
  .contact__role {
    font-size: 14px; margin: 2px 0 10px 8px;
  }
  .contact__address {
    font-size: 14px; line-height: 1.4; margin-left: 14px; margin-bottom: 8px;
  }
  .contact__list { list-style: none; margin-left: 14px; }
  .contact__item {
    display: flex; align-items: center; gap: 10px;
    font-size: 14px; line-height: 1.6;
  }
  .contact__item svg { width: 13px; height: 13px; flex: none; }
  .contact__item .accent { color: var(--blue); }
</style>
</head>
<body>
<main class="canvas">

  <section class="card card--back" aria-label="Card back">
    <div class="back-brand">
      <div class="back-brand__dot"></div>
      <div class="back-brand__name">Lumenreach Media</div>
    </div>
    <p class="back-url">www.<span>lumenreachmedia</span>.com</p>
  </section>

  <section class="card card--front" aria-label="Card front">
    <div class="front-brand">
      <div class="front-brand__dot"></div>
      <div class="front-brand__name">Lumenreach Media</div>
    </div>

    <div class="divider"></div>

    <div class="contact">
      <h1 class="contact__name">Marcus Hale</h1>
      <p class="contact__role">Director</p>
      <p class="contact__address">PO Box 517 Eastbrook<br>NSW Australia 2093</p>
      <ul class="contact__list">
        <li class="contact__item">
          <svg viewBox="0 0 16 16" fill="var(--blue)"><path d="M3.6 1.2l2.3 2.6-1.2 2a9 9 0 0 0 5.5 5.5l2-1.2 2.6 2.3-1.4 2.1C7.3 14.4 1.6 8.7 1.5 2.6z"/></svg>
          +330 5184-2209
        </li>
        <li class="contact__item">
          <svg viewBox="0 0 16 16" fill="var(--blue)"><rect x="4" y="1" width="8" height="4"/><rect x="1" y="6" width="14" height="6" rx="1"/><rect x="4" y="10" width="8" height="5"/></svg>
          +330 5184-2210
        </li>
        <li class="contact__item">
          <svg viewBox="0 0 16 16" fill="none" stroke="var(--blue)" stroke-width="1.6"><rect x="1.5" y="3.5" width="13" height="9"/><path d="M1.5 3.5l6.5 5 6.5-5"/></svg>
          info@lumenreachmedia.com
        </li>
        <li class="contact__item">
          <svg viewBox="0 0 16 16" fill="none" stroke="var(--blue)" stroke-width="1.4"><circle cx="8" cy="8" r="6.5"/><ellipse cx="8" cy="8" rx="3" ry="6.5"/><path d="M1.5 8h13"/></svg>
          <span>www.<span class="accent">lumenreachmedia</span>.com</span>
        </li>
      </ul>
    </div>
  </section>

</main>
</body>
</html>
```